I have a logo and need to design the business card and stationery.
Updates

The uploaded logo image named as GREYMARSH CONTRACTS which is to be replaced to GREYMARSH CONTRACTS. Kindly add below details and submit the designs- Company name- Greymarsh Engineering Contracts LLP Name & Post- Kelvan Joshi (Designated Partner) Address- Block No.317, Wing C, Tulvo Trade Court, Manek Pural Road, Ruparel Industrial Estate, Goregaon(E), Mumbai - 400 063 Contact- +91 97415 60382 Email- kelvanjoshi@mailbrook.example Website- www.greymarshcontracts.example Contact for Letterhead- +91-22-28754193

Hi Tovin Rahul, We are liking your Design #28860835. We have suggested some changes which are mentioned in feedback. Kindly revert with it asap to finalize this design.

Colors

Designer to choose colors to be used in the design.

```html
<!DOCTYPE html>
<html lang="en">
<head>
<meta charset="utf-8">
<title>Greymarsh Contracts – Business Card</title>
<link rel="stylesheet" href="https://fonts.googleapis.com/css2?family=Roboto:wght@400;700&display=swap">
<style>
  :root {
    --backdrop: #e4e4e4;
    --card: #2f2f31;
    --card-deep: #1f1f21;
    --white: #ffffff;
    --muted: #8a8a8c;
    --line-grey: #6d6d70;
  }
  * { margin: 0; padding: 0; box-sizing: border-box; }
  html, body { width: 1200px; height: 802px; overflow: hidden; }
  body {
    background: var(--backdrop);
    font-family: "Roboto", Arial, sans-serif;
    display: flex;
    align-items: center;
    justify-content: center;
    gap: 40px;
  }
  .card {
    position: relative;
    width: 540px;
    height: 310px;
    background: var(--card);
    overflow: hidden;
    box-shadow: 0 6px 18px rgba(0,0,0,.18);
  }
  /* Front */
  .brand-mark {
    position: absolute; left: 34px; top: 64px;
    width: 48px; height: 48px; background: var(--white);
  }
  .brand-row, .sub-row {
    position: absolute; left: 0; right: 0;
    display: flex; align-items: center;
  }
  .brand-row { top: 122px; height: 28px; }
  .sub-row { top: 152px; height: 14px; }
  .band-stub { width: 26px; height: 13px; background: var(--white); flex: none; }
  .band-main { flex: 1; height: 13px; background: var(--white); margin-left: 10px; }
  .rule-stub { width: 26px; height: 3px; background: var(--line-grey); flex: none; }
  .rule-main { flex: 1; height: 3px; background: var(--line-grey); margin-left: 10px; }
  .brand-name {
    margin-left: 8px; color: var(--white); font-weight: 700;
    font-size: 24px; line-height: 28px; letter-spacing: .5px; white-space: nowrap;
  }
  .brand-sub {
    margin-left: 8px; color: var(--white); font-weight: 700;
    font-size: 11.5px; line-height: 14px; letter-spacing: 7.4px; white-space: nowrap;
  }
  .holder {
    position: absolute; right: 32px; top: 58px; text-align: right;
  }
  .holder .person { color: var(--white); font-weight: 700; font-size: 15px; letter-spacing: .3px; }
  .holder .role { color: var(--muted); font-size: 11px; margin-top: 3px; }
  .contacts {
    position: absolute; left: 34px; bottom: 30px;
    list-style: none; color: var(--muted); font-size: 11.5px;
  }
  .contacts li { display: flex; align-items: center; gap: 9px; margin-top: 6px; }
  .contacts svg { width: 11px; height: 11px; flex: none; }
  .address {
    position: absolute; right: 32px; bottom: 30px; text-align: right;
    color: var(--line-grey); font-size: 11.5px; line-height: 1.55; font-style: normal;
  }
  /* Back */
  .card-back { background: var(--card-deep); }
  .pattern-field {
    position: absolute; inset: 0;
    background: linear-gradient(135deg, #3a3a3d 0%, #262628 45%, #161617 100%);
  }
  .back-mark {
    position: absolute; right: 44px; top: 170px;
    display: flex; align-items: center; gap: 10px;
    color: var(--white); font-weight: 700; font-size: 15px; letter-spacing: .5px;
  }
  .back-mark .mark-square { width: 34px; height: 34px; background: var(--white); }
</style>
</head>
<body>
  <section class="card card-front" aria-label="Business card front">
    <div class="brand-mark"></div>

    <div class="brand-row">
      <div class="band-stub"></div>
      <div class="brand-name">GREYMARSH</div>
      <div class="band-main"></div>
    </div>
    <div class="sub-row">
      <div class="rule-stub"></div>
      <div class="brand-sub">CONTRACTS</div>
      <div class="rule-main"></div>
    </div>

    <div class="holder">
      <div class="person">KELVAN JOSHI</div>
      <div class="role">Designated Partner</div>
    </div>

    <ul class="contacts">
      <li>
        <svg viewBox="0 0 12 12"><circle cx="6" cy="6" r="6" fill="#fff"/><path d="M4 3.2l1 1.6-.6.6c.4.9 1 1.5 1.9 1.9l.6-.6 1.6 1-.5 1.1C6 8.6 3.4 6 3.2 3.7z" fill="#2f2f31"/></svg>
        +91 97415 60382
      </li>
      <li>
        <svg viewBox="0 0 12 12"><rect x="0" y="2" width="12" height="8" fill="#fff"/><path d="M0 2l6 4.5L12 2" fill="none" stroke="#2f2f31" stroke-width="1"/></svg>
        kelvanjoshi@mailbrook.example
      </li>
      <li>
        <svg viewBox="0 0 12 12"><circle cx="6" cy="6" r="6" fill="#fff"/><circle cx="6" cy="6" r="3.2" fill="none" stroke="#2f2f31" stroke-width="1"/><path d="M2.8 6h6.4" stroke="#2f2f31" stroke-width="1"/></svg>
        www.greymarshcontracts.example
      </li>
    </ul>

    <address class="address">
      Block No.317, Wing C<br>
      Tulvo Trade Court, Manek Pural Road<br>
      Ruparel Industrial Estate<br>
      Goregaon(E), Mumbai - 400 063
    </address>
  </section>

  <section class="card card-back" aria-label="Business card back">
    <div class="pattern-field" role="img" aria-label="Embossed repeating square tile pattern in dark greys covering the card back"></div>
    <div class="back-mark">
      <div class="mark-square"></div>
      <span>GREYMARSH CONTRACTS</span>
    </div>
  </section>
</body>
</html>
```